Kestrel Facilities Business Card Design

We would now like to design business cards with the new Kestrel Facilities logo

Target Market(s)

Professional

Industry/Entity Type

Professional services

Contact Information for Business Card

Employee name, title, phone number, email address, corporate office address and logo.

Font styles to use
Sans Serif

Colors
0054AA
0677BA
7BADD7
CADEEF
E8F1F8

Requirements
Must have
• My logo
Should not have
• any other pictures or images besides my logo

```html
<!DOCTYPE html>
<html lang="en">
<head>
<meta charset="utf-8">
<title>Kestrel Facilities Business Card</title>
<link href="https://fonts.googleapis.com/css2?family=Montserrat:wght@400;500;700;800&display=swap" rel="stylesheet">
<style>
  :root {
    --brand-blue: #3575bd;
    --swoosh-grey: #a0a0a0;
    --paper: #ffffff;
    --ink: #1b1b1b;
    --logo-light: #cadeef;
    --stage: #1e1f21;
  }
  * { margin: 0; padding: 0; box-sizing: border-box; }
  html, body {
    width: 1200px; height: 900px; overflow: hidden;
    background: var(--stage);
    font-family: "Montserrat", sans-serif;
  }
  .sheet {
    width: 1200px; height: 900px;
    display: flex; flex-direction: column; align-items: center; justify-content: center;
    gap: 50px;
  }
  .card {
    position: relative;
    width: 630px; height: 360px;
    border-radius: 22px;
    overflow: hidden;
  }
  .card-front { background: var(--paper); }
  .card-back { background: var(--brand-blue); display: flex; align-items: center; justify-content: center; }
  .front-shapes { position: absolute; inset: 0; }
  .holder {
    position: absolute; left: 40px; top: 14px;
    color: var(--paper);
  }
  .holder-name { font-weight: 800; font-size: 21px; line-height: 26px; letter-spacing: 0.5px; text-transform: uppercase; }
  .holder-title { font-weight: 400; font-size: 14px; line-height: 18px; }
  .address {
    position: absolute; left: 40px; top: 172px;
    color: var(--ink); font-size: 15px; line-height: 20px; font-weight: 500;
  }
  .contacts {
    position: absolute; left: 40px; top: 228px;
    list-style: none; color: var(--ink); font-size: 15px; font-weight: 500;
  }
  .contacts li { display: flex; align-items: center; gap: 8px; height: 22px; }
  .contacts svg { width: 14px; height: 14px; fill: var(--brand-blue); flex: none; }
  .brand-name {
    font-weight: 800; text-transform: uppercase; letter-spacing: 1px;
  }
  .card-front .brand-name {
    position: absolute; right: 44px; bottom: 40px;
    color: var(--brand-blue); font-size: 30px; line-height: 1.05; text-align: left;
  }
  .card-back .brand-name {
    color: var(--logo-light); font-size: 46px; line-height: 1.05;
  }
</style>
</head>
<body>
<main class="sheet">
  <section class="card card-front">
    <svg class="front-shapes" viewBox="0 0 630 360" preserveAspectRatio="none" aria-hidden="true">
      <path d="M0 0 H630 V95 C600 80 560 78 500 82 C380 90 250 100 180 98 C110 96 70 88 0 78 Z" fill="var(--brand-blue)"/>
      <path d="M0 88 C70 98 110 106 180 108 C250 110 380 100 500 92 C540 89 575 88 600 90 C560 100 500 110 420 120 C300 135 200 150 120 150 C70 150 30 140 0 130 Z" fill="var(--swoosh-grey)"/>
    </svg>
    <div class="holder">
      <div class="holder-name">Dana Whitfield</div>
      <div class="holder-title">Co-Founder</div>
    </div>
    <div class="address">
      <div>418 Harbor View Road</div>
      <div>Suite 210 Millbrook 42</div>
    </div>
    <ul class="contacts">
      <li>
        <svg viewBox="0 0 24 24"><path d="M6.6 10.8a15.1 15.1 0 0 0 6.6 6.6l2.2-2.2a1 1 0 0 1 1-.25 11.4 11.4 0 0 0 3.6.57 1 1 0 0 1 1 1V20a1 1 0 0 1-1 1A17 17 0 0 1 3 4a1 1 0 0 1 1-1h3.5a1 1 0 0 1 1 1c0 1.25.2 2.45.57 3.6a1 1 0 0 1-.25 1z"/></svg>
        <span>+254-700-41236</span>
      </li>
      <li>
        <svg viewBox="0 0 24 24"><path d="M2 5h20v14H2z"/><path d="M3 6l9 7 9-7" fill="none" stroke="#fff" stroke-width="1.6"/></svg>
        <span>info@kestrelfm.com</span>
      </li>
      <li>
        <svg viewBox="0 0 24 24"><circle cx="12" cy="12" r="10"/><path d="M2 12h20M12 2c3 3 3 17 0 20M12 2c-3 3-3 17 0 20" fill="none" stroke="#fff" stroke-width="1.3"/></svg>
        <span>www.kestrelfm.com</span>
      </li>
    </ul>
    <div class="brand-name">Kestrel<br>Facilities</div>
  </section>

  <section class="card card-back">
    <div class="brand-name">Kestrel<br>Facilities</div>
  </section>
</main>
</body>
</html>
```